Vernac Law Business cards and stationary design project

We are looking for a stationary design for business cards (double sided), 8x10, 5x7, and legal and standard envelopes.

We would like the design to match the logo that we have already.
Color palate preferred is Teal, White, grey and any others that will look good for a professional law firm.

We would like this statement: "RELATIONSHIPS. RESPECT. RESULT" to be on the back of the business cards and maybe on the stationary if it looks good.

Please see link to website for more information: www.vernac-law.example

Target Market(s)

Potential clients that need Attorney services.

Industry/Entity Type

Law Firm

Contact Information for Business Card

We would like the front and back to be two different colors. Current business cards are teal front, grey back and are a vertical design. We are open to options with colors.

Font styles to use
Serif

Colors
33a6d7
33b8a4
b9b9b9
5c5c5c

Requirements
Must have
• Logo supplied needs to go on the card and stationary.
• Match website color palate, www.vernac-law.example
• Be professional and not too wordy.
• Criminal Law, Civil Litigation, Personal Injury, Restraining Orders need to be on the card.
Nice to have
• RELATIONSHIPS. RESPECT. RESULTS. on the back of the card.
Should not have
• Not be too busy/wordy or too flashy.

```html
<!DOCTYPE html>
<html lang="en">
<head>
<meta charset="utf-8">
<title>Vernac Law – Business Cards</title>
<link rel="stylesheet" href="https://fonts.googleapis.com/css2?family=Cinzel:wght@400;600&family=Open+Sans:wght@400;600&display=swap">
<style>
  :root {
    --teal: #33a6b3;
    --teal-bright: #33b8a4;
    --grey-light: #b9b9b9;
    --grey-dark: #5c5c5c;
    --charcoal: #2f3031;
    --charcoal-deep: #232425;
    --paper: #fbfbfb;
    --backdrop: #e9e7e4;
    --ink: #4a4a4a;
  }
  * { box-sizing: border-box; margin: 0; padding: 0; }
  html, body { width: 1200px; height: 800px; overflow: hidden; }
  body {
    background: var(--backdrop);
    position: relative;
    font-family: "Open Sans", Arial, sans-serif;
  }
  .card {
    position: absolute;
    top: 245px;
    width: 520px;
    height: 310px;
    border-radius: 3px;
    box-shadow: 0 10px 28px rgba(0,0,0,0.22);
    overflow: hidden;
  }

  /* Front: white contact card */
  .card-front { left: 50px; background: var(--paper); }
  .card-front .edge-band {
    position: absolute; left: 0; top: 0; width: 100%; height: 14px;
    background: var(--charcoal);
  }
  .card-front .divider {
    position: absolute; left: 0; right: 0; top: 96px;
    height: 1px; background: var(--grey-light);
  }
  .card-front .person {
    position: absolute; left: 34px; top: 44px;
  }
  .card-front .person-name {
    font-family: "Cinzel", Georgia, serif;
    font-size: 21px; color: var(--teal); letter-spacing: 0.5px;
  }
  .card-front .person-role {
    font-size: 10px; color: var(--grey-light); letter-spacing: 1.5px;
    text-transform: uppercase; margin-top: 2px;
  }
  .card-front .contacts {
    position: absolute; left: 34px; top: 118px;
    list-style: none; font-size: 12px; color: var(--grey-dark); line-height: 22px;
  }
  .card-front .contacts b {
    display: inline-block; width: 26px; color: var(--teal); font-weight: 600;
  }
  .card-front .firm-mark {
    position: absolute; right: 40px; top: 140px;
    display: flex; align-items: center; gap: 10px;
  }
  .card-front .firm-mark .square {
    width: 12px; height: 12px; background: var(--teal);
  }
  .card-front .firm-mark .firm-name {
    font-family: "Cinzel", Georgia, serif;
    font-size: 26px; color: var(--teal); letter-spacing: 1px;
  }
  .card-front .address {
    position: absolute; left: 34px; bottom: 22px;
    font-size: 12px; color: var(--grey-dark); line-height: 18px;
  }

  /* Back: charcoal card */
  .card-back {
    left: 630px;
    background: linear-gradient(135deg, var(--charcoal-deep), var(--charcoal) 55%, #3a3b3c);
  }
  .card-back .firm-name {
    position: absolute; right: 34px; top: 36px;
    font-family: "Cinzel", Georgia, serif;
    font-size: 30px; color: var(--teal); letter-spacing: 1px;
  }
  .card-back .firm-rule {
    position: absolute; right: 34px; top: 84px; width: 250px; height: 1px;
    background: var(--teal);
  }
  .card-back .tagline-rule {
    position: absolute; left: 30px; right: 30px; height: 1px; background: var(--teal);
  }
  .card-back .tagline-rule.upper { top: 112px; }
  .card-back .tagline-rule.lower { top: 150px; }
  .card-back .tagline {
    position: absolute; left: 30px; right: 30px; top: 118px;
    font-family: "Cinzel", Georgia, serif; font-weight: 600;
    font-size: 19px; color: #e8e8e8; letter-spacing: 1.5px; text-align: center;
  }
  .card-back .practice {
    position: absolute; right: 34px; bottom: 28px;
    list-style: none; text-align: right;
    font-size: 13px; line-height: 21px; color: #d6d6d6;
  }
  .card-back .practice li::after {
    content: ""; display: inline-block; width: 6px; height: 6px;
    border-radius: 50%; background: var(--teal); margin-left: 8px; vertical-align: middle;
  }
</style>
</head>
<body>

<section class="card card-front" aria-label="Business card front">
  <div class="edge-band"></div>
  <div class="person">
    <p class="person-name">Maren Vernac</p>
    <p class="person-role">Lawyer</p>
  </div>
  <div class="divider"></div>
  <ul class="contacts">
    <li><b>[P]</b>(555) 014-2238</li>
    <li><b>[E]</b>maren@vernac-law.example</li>
    <li><b>[W]</b>www.vernac-law.example</li>
  </ul>
  <div class="firm-mark">
    <span class="square"></span>
    <span class="firm-name">Vernac Law</span>
  </div>
  <p class="address">Southern California<br>450 Harbor View Ave. #200<br>Bayside, CA 90000</p>
</section>

<section class="card card-back" aria-label="Business card back">
  <p class="firm-name">Vernac Law</p>
  <div class="firm-rule"></div>
  <div class="tagline-rule upper"></div>
  <p class="tagline">Relationships. Respect. Results.</p>
  <div class="tagline-rule lower"></div>
  <ul class="practice">
    <li>Practice areas</li>
    <li>Criminal Law</li>
    <li>Restraining Orders</li>
    <li>Civil Litigation/Personal Injury</li>
  </ul>
</section>

</body>
</html>
```